Modern Medical Optometry Website

We need mordern, Patient friendly website. Easy to navigate and enhance our advance medical technology and excellent patient care.
1. HOME PAGE
2. OUR TEAM PAGE
3. EYECARE PAGE - VISION SERVICES, EYE EXAMS, KERATOCONUS CENTER, GLAUCOMA , DIABITES, MELORIDEX EXAM, DIGITAL RETINAL, OCT.
4. MYOPIA CONTROL CLINIC
5. DRY EYE CLINIC
6. EYEWEAR
7. PATIENT CENTER - BLOG
7. CONTACT US
This is our current website www.brivaloka.com
and We want to add more content and a cleaner design like these website
http://tarnwickfolvendale.com/
https://www.qmvorlu.com/

```html
<!DOCTYPE html>
<html lang="en">
<head>
<meta charset="utf-8">
<title>Lumivar Optometry</title>
<link rel="stylesheet" href="https://fonts.googleapis.com/css2?family=Montserrat:wght@400;600;700&family=Raleway:wght@400;500&family=Lato:wght@400;700&display=swap">
<style>
:root{
  --teal:#0f8bb0;
  --teal-dark:#0b6f8f;
  --yellow:#f9dd55;
  --yellow-strong:#f7d51e;
  --ink:#111;
  --text:#444;
  --nav:#8a8a8a;
  --white:#fff;
}
*{margin:0;padding:0;box-sizing:border-box}
html,body{width:707px;height:1200px;overflow:hidden;background:var(--white)}
body{position:relative;font-family:"Lato",sans-serif;color:var(--text)}
.abs{position:absolute}

.topbar{left:0;top:0;width:707px;height:31px;background:var(--teal);color:var(--white);font-family:"Raleway",sans-serif;font-size:8.6px}
.topbar .cell{position:absolute;top:0;height:31px;border-left:1px solid rgba(255,255,255,.25);display:flex;align-items:center;gap:7px;padding-left:12px}
.topbar .social{padding:0;justify-content:center}
.topbar .social span{width:7px;height:7px;border-radius:50%;background:var(--yellow-strong)}

.header{left:0;top:31px;width:707px;height:79px;background:var(--white)}
.brand{left:44px;top:7px;width:82px;height:112px;border-radius:50%;background:var(--white);border:2px solid var(--yellow-strong);display:flex;align-items:center;justify-content:center;z-index:3}
.brand span{font-family:"Raleway",sans-serif;font-size:8px;color:var(--teal-dark);letter-spacing:.5px;text-align:center;line-height:1.3}
.nav{left:130px;top:66px;display:flex;gap:21px;font-family:"Raleway",sans-serif;font-size:10px;color:var(--nav);text-transform:uppercase}
.nav .active{color:var(--teal)}

.hero{left:0;top:110px;width:707px;height:338px;background:linear-gradient(100deg,#1f8fab 0%,#2b9dba 45%,#6cc3d6 100%)}
.hero-title{left:47px;top:78px;font-family:"Montserrat",sans-serif;font-weight:600;font-size:37px;line-height:40px;color:var(--white);letter-spacing:1px;text-shadow:1px 2px 3px rgba(0,0,0,.35)}
.hero-copy{left:47px;top:164px;width:260px;font-size:8.4px;line-height:15.4px;color:var(--white)}
.btn{left:45px;top:228px;width:141px;height:31px;background:var(--yellow-strong);color:#222;font-family:"Raleway",sans-serif;font-size:10px;display:flex;align-items:center;justify-content:center}
.hero-visual{left:328px;top:17px;width:306px;height:306px}

.services{left:0;top:448px;width:707px;height:471px;display:grid;grid-template-columns:repeat(3,1fr);grid-template-rows:repeat(3,157px)}
.tile{position:relative;display:flex;align-items:center;justify-content:center;text-align:center;font-family:"Montserrat",sans-serif;font-weight:700;font-size:20.5px;line-height:27px;color:var(--ink);text-transform:uppercase}
.tile .photo{position:absolute;inset:0}
.tile b{position:relative;font-weight:700}

.footer{left:0;top:919px;width:707px;height:281px;background:var(--yellow)}
.col{position:absolute;top:42px;font-size:8.6px;color:#333}
.col h3{font-family:"Lato",sans-serif;font-weight:700;font-size:12.5px;color:var(--teal);margin-bottom:12px}
.row{display:flex;gap:12px;align-items:flex-start;height:25px;line-height:11px}
.row svg{flex:none;width:12px;height:11px}
.row.tall{height:36px;line-height:15px}
.dir{position:absolute;width:164px;height:25px;border-radius:13px;background:#222;color:var(--white);font-size:8.6px;display:flex;align-items:center;padding-left:10px;gap:12px}
.hours p{line-height:18.4px}
.hours strong{font-weight:700;color:#222}
.circles{display:flex;gap:6px;margin-top:22px}
.circles span{width:24px;height:24px;border-radius:50%;background:#222}
.circles span:first-child{background:var(--teal)}
.rule{left:0;top:239px;width:707px;height:1px;background:rgba(0,0,0,.08)}
.copy{left:0;top:254px;width:707px;text-align:center;font-size:7.6px;color:#666}
.copy strong{color:var(--teal)}
</style>
</head>
<body>

<div class="abs topbar">
  <div class="cell" style="left:273px;width:101px">
    <svg width="10" height="10" viewBox="0 0 24 24"><path d="M6.6 2h3l1.6 5-2.2 1.6a12 12 0 0 0 6.4 6.4L17 12.8l5 1.6v3a3 3 0 0 1-3 3A17 17 0 0 1 3.6 5 3 3 0 0 1 6.6 2z" fill="none" stroke="#f7d51e" stroke-width="2"/></svg>
    555-210-4418
  </div>
  <div class="cell" style="left:373px;width:166px">
    <svg width="12" height="9" viewBox="0 0 24 18"><rect x="1" y="1" width="22" height="16" fill="none" stroke="#f7d51e" stroke-width="2"/><path d="M1 1l11 9 11-9" fill="none" stroke="#f7d51e" stroke-width="2"/></svg>
    info@lumivaroptometry.com
  </div>
  <div class="cell social" style="left:539px;width:31px"><span></span></div>
  <div class="cell social" style="left:570px;width:31px"><span></span></div>
  <div class="cell social" style="left:601px;width:31px"><span></span></div>
  <div class="cell social" style="left:632px;width:30px;border-right:1px solid rgba(255,255,255,.25)"><span></span></div>
</div>

<div class="abs header"></div>
<div class="abs brand"><span>LUMIVAR<br>OPTOMETRY</span></div>
<nav class="abs nav">
  <span>Home</span><span class="active">Our Team</span><span>Eye Care</span><span>Myopia Control Clinic</span><span>Eyewear</span><span>Blog</span><span>Contact Us</span>
</nav>
<svg class="abs" style="left:649px;top:64px" width="13" height="13" viewBox="0 0 24 24"><circle cx="10" cy="10" r="7.5" fill="none" stroke="#0f8bb0" stroke-width="2"/><path d="M15.5 15.5L22 22" stroke="#0f8bb0" stroke-width="2"/></svg>

<section class="abs hero" role="img" aria-label="Patient at an eye examination slit lamp, teal tinted background">
  <h1 class="abs hero-title">LUMIVAR<br>SERVICES</h1>
  <p class="abs hero-copy">Lorem ipsum dolor sit amet, consectetur adipiscing elit, sed aliqua. Ut enim ad minim veniam, quis nostrud exercitation ullamco laboris nisi ut aliquip ex ea commodo consequat.</p>
  <a class="abs btn">MAKE AN APPOINTMENT</a>
  <svg class="abs hero-visual" viewBox="0 0 306 306">
    <defs>
      <radialGradient id="lamp" cx="55%" cy="45%" r="60%">
        <stop offset="0" stop-color="#fdf7ee"/>
        <stop offset=".5" stop-color="#c9d3d8"/>
        <stop offset="1" stop-color="#5b6f78"/>
      </radialGradient>
    </defs>
    <circle cx="153" cy="153" r="152" fill="#1a7c99" opacity=".55"/>
    <circle cx="153" cy="153" r="146" fill="url(#lamp)" role="img" aria-label="Close view of a patient looking into a slit lamp"/>
    <circle cx="153" cy="153" r="122" fill="none" stroke="#f7d51e" stroke-width="13"/>
  </svg>
</section>

<section class="abs services">
  <div class="tile"><div class="photo" role="img" aria-label="Children swimming underwater in goggles" style="background:linear-gradient(135deg,#7fd3ef,#9fdcef 60%,#c9e9f1)"></div><b>Myopia<br>Control Clinic</b></div>
  <div class="tile"><div class="photo" role="img" aria-label="Close view of an eye with a contact lens" style="background:linear-gradient(135deg,#d8d3d6,#eeeaec 60%,#f6f4f5)"></div><b>Speciality<br>Contact Lens</b></div>
  <div class="tile"><div class="photo" role="img" aria-label="Eye drop being applied to an eye" style="background:linear-gradient(135deg,#b9c9d8,#e5e0e1 55%,#efe9e8)"></div><b>Dry Eye<br>Clinic</b></div>
  <div class="tile"><div class="photo" role="img" aria-label="Retinal scan on a monitor beside an eye exam device" style="background:linear-gradient(135deg,#d9a168,#e6e2df 55%,#f0efee)"></div><b>Diabetes Exam</b></div>
  <div class="tile"><div class="photo" role="img" aria-label="Woman covering one eye during an eye exam" style="background:linear-gradient(135deg,#c7b6b2,#d6d3d3 55%,#c9c9cb)"></div><b>Eye Exam</b></div>
  <div class="tile"><div class="photo" role="img" aria-label="Close view of an irritated red eye" style="background:linear-gradient(135deg,#8f8a8a,#c2b7b4 55%,#d7cfcb)"></div><b>Urgent Red<br>Eye Center</b></div>
  <div class="tile"><div class="photo" role="img" aria-label="Older patient at an eye examination instrument" style="background:linear-gradient(135deg,#ddd6d2,#eeebea 55%,#f4f3f3)"></div><b>Gluecome Exam</b></div>
  <div class="tile"><div class="photo" role="img" aria-label="Tired person holding glasses in front of a screen" style="background:linear-gradient(135deg,#cfcbcb,#e9e7e7 55%,#dedcdd)"></div><b>Computer<br>Vision<br>Syndrome</b></div>
  <div class="tile"><div class="photo" role="img" aria-label="Surgeon performing laser eye surgery" style="background:linear-gradient(135deg,#c9d6ea,#e4d6e2 55%,#c2d2e5)"></div><b>Lasik<br>Management</b></div>
</section>

<footer class="abs footer">
  <div class="col" style="left:47px">
    <h3>Lumivar Optometry</h3>
    <div class="row"><svg viewBox="0 0 24 24"><path d="M6.6 2h3l1.6 5-2.2 1.6a12 12 0 0 0 6.4 6.4L17 12.8l5 1.6v3a3 3 0 0 1-3 3A17 17 0 0 1 3.6 5 3 3 0 0 1 6.6 2z" fill="#0f8bb0"/></svg>555-210-4418</div>
    <div class="row"><svg viewBox="0 0 24 24"><rect x="2" y="8" width="20" height="13" rx="2" fill="#0f8bb0"/><rect x="7" y="2" width="10" height="8" fill="#0f8bb0"/></svg>555-210-4479</div>
    <div class="row"><svg viewBox="0 0 24 18"><rect x="0" y="1" width="24" height="16" rx="1" fill="#0f8bb0"/><path d="M0 2l12 8 12-8" fill="none" stroke="#f9dd55" stroke-width="2"/></svg>info@brivaloka.com</div>
    <div class="row tall"><svg viewBox="0 0 24 24"><path d="M12 1a8 8 0 0 1 8 8c0 6-8 14-8 14S4 15 4 9a8 8 0 0 1 8-8z" fill="#0f8bb0"/><circle cx="12" cy="9" r="3" fill="#f9dd55"/></svg>4821 Corlan Ave., Dunmere,<br>CA 90412</div>
  </div>
  <div class="dir" style="left:46px;top:177px">Get directions on the map <svg width="18" height="6" viewBox="0 0 18 6"><path d="M0 3h16M13 0.5l3 2.5-3 2.5" fill="none" stroke="#0f8bb0" stroke-width="1.2"/></svg></div>

  <div class="col" style="left:256px">
    <h3>Ashvale Hills</h3>
    <div class="row"><svg viewBox="0 0 24 24"><path d="M6.6 2h3l1.6 5-2.2 1.6a12 12 0 0 0 6.4 6.4L17 12.8l5 1.6v3a3 3 0 0 1-3 3A17 17 0 0 1 3.6 5 3 3 0 0 1 6.6 2z" fill="#0f8bb0"/></svg>555-316-7052</div>
    <div class="row"><svg viewBox="0 0 24 18"><rect x="0" y="1" width="24" height="16" rx="1" fill="#0f8bb0"/><path d="M0 2l12 8 12-8" fill="none" stroke="#f9dd55" stroke-width="2"/></svg>ashvale@brivaloka.com</div>
    <div class="row tall"><svg viewBox="0 0 24 24"><path d="M12 1a8 8 0 0 1 8 8c0 6-8 14-8 14S4 15 4 9a8 8 0 0 1 8-8z" fill="#0f8bb0"/><circle cx="12" cy="9" r="3" fill="#f9dd55"/></svg>2290 Fenwick St.,Suite 4,<br>Ashvale Hills, CA 90468</div>
  </div>
  <div class="dir" style="left:256px;top:177px">Get directions on the map <svg width="18" height="6" viewBox="0 0 18 6"><path d="M0 3h16M13 0.5l3 2.5-3 2.5" fill="none" stroke="#0f8bb0" stroke-width="1.2"/></svg></div>

  <div class="col hours" style="left:466px">
    <h3>Opening Hours</h3>
    <p>Monday - Thursday : <strong>9 am - 6 pm</strong></p>
    <p>Friday : <strong>8.30 am - 5 pm</strong></p>
    <p>Saturday &nbsp;: <strong>8.30 am- 5 pm</strong></p>
    <p>Closed on <strong>Sundays</strong></p>
    <p style="line-height:11px;margin-top:4px">Please keep in mind we are closed<br>for <strong>lunch 1-2 pm</strong></p>
    <div class="circles"><span></span><span></span><span></span><span></span></div>
  </div>

  <div class="abs rule"></div>
  <p class="abs copy">Copyright © <strong>LUMIVAR OPTOMETRY</strong> - 2019 . All right Rereserved</p>
</footer>

</body>
</html>
```